Fern Gate book design

I would like a new cover design to my book Fern Gate. It is a self help book for teenagers that I give away in public schools while I speak on suicide prevention type topics. I will send you the current cover that has the Fern Gate logo on it. The tag line now says, "raising the value of human life" I want to change that to, "Understanding your true value."

```html
<!DOCTYPE html>
<html lang="en">
<head>
<meta charset="utf-8">
<title>Fern Gate – Book Cover</title>
<link rel="stylesheet" href="https://fonts.googleapis.com/css2?family=Open+Sans:wght@400;600;700&display=swap">
<style>
  :root {
    --backdrop: #282828;
    --cover-top: #f1f0ef;
    --cover-mid: #e2e1e0;
    --cover-low: #e6e4e2;
    --crowd-warm: #d6cdc4;
    --crowd-deep: #c9c0b8;
    --ink-grey: #4a4a4a;
    --ink-dark: #222222;
    --accent-red: #9b0b0b;
  }
  * { margin: 0; padding: 0; box-sizing: border-box; }
  html, body {
    width: 1200px;
    height: 1200px;
    overflow: hidden;
    background: var(--backdrop);
    font-family: "Open Sans", sans-serif;
  }
  .book-cover {
    position: absolute;
    left: 248px;
    top: 55px;
    width: 704px;
    height: 1090px;
    overflow: hidden;
    background: linear-gradient(180deg, var(--cover-top) 0%, var(--cover-mid) 45%, var(--cover-low) 100%);
  }
  .crowd-photo {
    position: absolute;
    left: 0;
    bottom: 0;
    width: 100%;
    height: 440px;
    background:
      linear-gradient(180deg, rgba(230,228,226,1) 0%, rgba(230,228,226,0) 35%),
      radial-gradient(ellipse at 70% 60%, var(--crowd-deep) 0%, var(--crowd-warm) 55%, var(--cover-low) 100%);
  }
  .title-block {
    position: absolute;
    left: 0;
    top: 330px;
    width: 100%;
    text-align: center;
  }
  .title-wordmark {
    font-weight: 700;
    font-size: 96px;
    line-height: 1;
    letter-spacing: 1px;
    color: var(--ink-grey);
  }
  .title-tagline {
    margin-top: 22px;
    font-weight: 400;
    font-size: 19px;
    color: var(--ink-dark);
  }
  .credits {
    position: absolute;
    left: 0;
    top: 975px;
    width: 100%;
    text-align: center;
  }
  .credits-authors {
    font-weight: 700;
    font-size: 21px;
    color: var(--accent-red);
  }
  .credits-foreword {
    margin-top: 10px;
    font-weight: 400;
    font-size: 14px;
    color: var(--ink-dark);
  }
</style>
</head>
<body>
  <main class="book-cover">
    <div class="crowd-photo" role="img" aria-label="Faded photograph of a crowd of young people with hands raised at an event"></div>
    <header class="title-block">
      <h1 class="title-wordmark">Fern Gate</h1>
      <p class="title-tagline">Understanding your True Value</p>
    </header>
    <footer class="credits">
      <p class="credits-authors">Ray Holloway with Owen Marsh</p>
      <p class="credits-foreword">Forward by Ridgeview survivor, Dana Whitlow</p>
    </footer>
  </main>
</body>
</html>
```